Business Card Design For Marketing Agnecy LVP

Need business card design for marketing agency.

Doug Fenwick
President, CEO
1-555-302-4196
doug@boldpromoperksgroup.example
www.BoldPromoPerksGroup.example

Back Side:
Boost Sales Using Rewards, Incentives & Giveaways
Get A Free Sample Package

Target Market(s)

B2B

Industry/Entity Type

Marketing

Contact Information for Business Card

Doug Fenwick
President, CEO
1-555-302-4196

Back Side:
Get A Free Sample Package

Please note that my current url is OLD DESIGN. I am working on new design and want the business card to match color themes at least on new site. Here is the demo link for new site so you can see the colors I use, etc.

http://layoutcratehub.example/kq/doug/lvp_final/index.html

Requirements
Must have
• Please note that my current url is OLD DESIGN. I am working on new design and want the business card to match color themes at least on new site. Here is the demo link for new site so you can see the colors I use, etc.

Nice to have

Should not have

```html
<!DOCTYPE html>
<html lang="en">
<head>
<meta charset="utf-8">
<title>LVP Business Card</title>
<link rel="stylesheet" href="https://fonts.googleapis.com/css2?family=Montserrat:wght@400;500;700;800&display=swap">
<style>
  :root {
    --brand-blue: #1176bd;
    --ink-grey: #4a4a4f;
    --paper: #ffffff;
    --backdrop: #d4d3d0;
    --rule: #ffffff;
  }
  * { box-sizing: border-box; margin: 0; padding: 0; }
  html, body { width: 1200px; height: 801px; overflow: hidden; }
  body {
    background: var(--backdrop);
    font-family: "Montserrat", sans-serif;
    position: relative;
  }
  .card {
    position: absolute;
    top: 246px;
    width: 540px;
    height: 309px;
    box-shadow: 0 6px 18px rgba(0,0,0,0.18);
  }
  /* Back side */
  .card-back {
    left: 40px;
    background: var(--brand-blue);
    color: var(--paper);
  }
  .card-back .wordmark {
    position: absolute;
    top: 66px;
    left: 0; right: 0;
    text-align: center;
    font-weight: 800;
    font-size: 78px;
    letter-spacing: 2px;
    line-height: 1;
  }
  .card-back .tagline-row {
    position: absolute;
    left: 0; right: 0;
    top: 214px;
    display: flex;
    align-items: center;
    gap: 10px;
  }
  .card-back .tagline-row .rule {
    flex: 1;
    height: 1px;
    background: var(--rule);
  }
  .card-back .tagline {
    font-size: 11.5px;
    font-weight: 500;
    white-space: nowrap;
  }
  .card-back .tagline .sep { opacity: 0.6; margin: 0 3px; }
  .card-back .site {
    position: absolute;
    top: 238px;
    left: 0; right: 0;
    text-align: center;
    font-size: 12px;
    font-weight: 500;
  }
  /* Front side */
  .card-front {
    left: 620px;
    background: var(--paper);
  }
  .card-front .wordmark {
    position: absolute;
    left: 30px;
    top: 116px;
    width: 190px;
    color: var(--brand-blue);
    font-weight: 800;
    font-size: 58px;
    line-height: 1;
  }
  .card-front .divider {
    position: absolute;
    left: 232px;
    top: 86px;
    width: 1px;
    height: 124px;
    background: var(--ink-grey);
  }
  .card-front .contact {
    position: absolute;
    left: 252px;
    top: 88px;
    color: var(--ink-grey);
  }
  .card-front .name {
    color: var(--brand-blue);
    font-weight: 800;
    font-size: 18px;
    text-transform: uppercase;
  }
  .card-front .title {
    font-size: 12.5px;
    margin: 2px 0 10px;
  }
  .card-front .line {
    display: flex;
    align-items: center;
    gap: 7px;
    font-size: 11.5px;
    margin-bottom: 5px;
    white-space: nowrap;
  }
  .card-front .line svg { width: 10px; height: 10px; fill: var(--brand-blue); flex: none; }
</style>
</head>
<body>
  <section class="card card-back">
    <div class="wordmark">LVP</div>
    <div class="tagline-row">
      <span class="rule"></span>
      <p class="tagline">Boost Sales Using Rewards<span class="sep">|</span>Incentives &amp; Giveaways<span class="sep">|</span>Get A Free Sample Package</p>
      <span class="rule"></span>
    </div>
    <p class="site">www.BoldPromoPerksGroup.example</p>
  </section>

  <section class="card card-front">
    <div class="wordmark">LVP</div>
    <span class="divider"></span>
    <div class="contact">
      <h1 class="name">Doug Fenwick</h1>
      <p class="title">President, CEO</p>
      <p class="line">
        <svg viewBox="0 0 10 10" aria-hidden="true"><path d="M2 0.5 L3.6 2.6 L2.7 3.6 C3.3 5 4.8 6.6 6.3 7.3 L7.3 6.3 L9.5 8 L8.3 9.5 C4.5 9.2 0.8 5.5 0.5 1.7 Z"/></svg>
        1-555-302-4196
      </p>
      <p class="line">
        <svg viewBox="0 0 10 10" aria-hidden="true"><path d="M0 2 H10 V8.5 H0 Z M0.6 2.4 L5 5.6 L9.4 2.4" stroke="#fff" stroke-width="0.7"/></svg>
        doug@boldpromoperksgroup.example
      </p>
      <p class="line">
        <svg viewBox="0 0 10 10" aria-hidden="true"><circle cx="5" cy="5" r="4.7"/><path d="M0.5 5 H9.5 M5 0.5 C2.5 3 2.5 7 5 9.5 M5 0.5 C7.5 3 7.5 7 5 9.5" stroke="#fff" stroke-width="0.6" fill="none"/></svg>
        www.BoldPromoPerksGroup.example
      </p>
    </div>
  </section>
</body>
</html>
```